Gift Cards in the Mail Envelope

Mailing out gift cards in the envelope. Need an eye popping envelope. Please look at the enclosed images. The envelope should look like that.

Low design quality

```html
<!DOCTYPE html>
<html lang="en">
<head>
<meta charset="UTF-8">
<title>Gift Card Envelope</title>
<link rel="stylesheet" href="https://fonts.googleapis.com/css2?family=Caveat:wght@500;700&display=swap">
<style>
  :root {
    --backdrop: #7a7c76;
    --envelope: #3f98e6;
    --envelope-light: #4aa3ec;
    --flap-line: #3185d6;
    --ink: #ffffff;
    --gift-yellow: #f2d93a;
    --gift-blue: #a7dbe9;
    --gift-green: #8fd858;
  }
  html, body {
    margin: 0;
    padding: 0;
    width: 1200px;
    height: 982px;
    overflow: hidden;
    background: var(--backdrop);
  }
  .canvas {
    position: relative;
    width: 1200px;
    height: 982px;
  }
  .envelope {
    position: absolute;
    top: 363px;
    width: 332px;
    height: 228px;
    background: linear-gradient(160deg, var(--envelope-light), var(--envelope));
    overflow: hidden;
  }
  .envelope--front { left: 252px; }
  .envelope--back { left: 627px; }
  .headline {
    position: absolute;
    left: 16px;
    top: 40px;
    margin: 0;
    font-family: "Caveat", cursive;
    font-weight: 500;
    color: var(--ink);
    font-size: 55px;
    line-height: 0.9;
    transform: rotate(-9deg);
    transform-origin: left top;
    z-index: 2;
  }
  .headline span { display: block; white-space: nowrap; }
  .headline .line-two { padding-left: 12px; letter-spacing: -1px; }
  .gift-art {
    position: absolute;
    left: 174px;
    top: 120px;
    width: 158px;
    height: 94px;
    border-radius: 4px;
    background: linear-gradient(120deg, rgba(242,217,58,0.55) 0%, rgba(167,219,233,0.55) 50%, rgba(143,216,88,0.5) 100%);
  }
  .back-art {
    position: absolute;
    inset: 0;
  }
  .flap-note {
    position: absolute;
    left: 126px;
    top: 44px;
    width: 80px;
    margin: 0;
    font-family: "Caveat", cursive;
    color: var(--ink);
    transform: rotate(-8deg);
    text-align: center;
    line-height: 0.9;
  }
  .flap-note .small { display: block; font-size: 12px; }
  .flap-note .big { display: block; font-size: 25px; font-weight: 700; }
</style>
</head>
<body>
<div class="canvas">
  <section class="envelope envelope--front">
    <h1 class="headline"><span>Amazing</span><span class="line-two">Gift Cards</span></h1>
    <div class="gift-art" role="img" aria-label="Illustration of wrapped gift boxes with bows, sparkles and confetti"></div>
  </section>

  <section class="envelope envelope--back">
    <svg class="back-art" width="332" height="228" viewBox="0 0 332 228">
      <path d="M0 0 L332 0 L304 78 Q298 90 284 90 L48 90 Q34 90 30 78 Z" fill="#4aa0ea" stroke="var(--flap-line)" stroke-width="1"/>
      <path d="M0 228 L34 90 M332 228 L298 90" stroke="var(--flap-line)" stroke-width="1" fill="none"/>
    </svg>
    <p class="flap-note"><span class="small">Open me</span><span class="big">Surprise!</span></p>
  </section>
</div>
</body>
</html>
```